- Redesign our business card
- Logo remains unchanged
- Current business card attached

Target Market(s)

We are a property management company

Industry/Entity Type

Business

```html
<!DOCTYPE html>
<html lang="en">
<head>
<meta charset="utf-8">
<title>Larchmere Consulting – Business Card</title>
<link href="https://fonts.googleapis.com/css2?family=Open+Sans:wght@400;600;700&display=swap" rel="stylesheet">
<style>
  :root {
    --stage: #000000;
    --card: #ffffff;
    --green-light: #97c23c;
    --green-mid: #6fa544;
    --green-deep: #3c8447;
    --brand-green: #4f9130;
    --white: #ffffff;
  }
  * { margin: 0; padding: 0; box-sizing: border-box; }
  html, body {
    width: 1200px; height: 900px; overflow: hidden;
    background: var(--stage);
    font-family: "Open Sans", Arial, sans-serif;
  }
  .canvas { position: relative; width: 1200px; height: 900px; }
  .card {
    position: absolute; top: 300px; width: 542px; height: 308px;
    background: var(--card); border-radius: 12px; overflow: hidden;
  }
  .card--front { left: 36px; }
  .card--back { left: 627px; }
  .band {
    position: absolute; left: 0; right: 0; top: 96px; height: 176px;
    background: linear-gradient(90deg, var(--green-light), var(--green-mid) 55%, var(--green-deep));
  }

  .brand { position: absolute; left: 43px; top: 22px; display: flex; align-items: center; gap: 10px; }
  .brand__dot {
    width: 58px; height: 58px; border-radius: 50%;
    background: var(--brand-green);
  }
  .brand__name { color: var(--brand-green); font-weight: 700; line-height: 1; }
  .brand__main { display: block; font-size: 25px; letter-spacing: 0.5px; }
  .brand__sub { display: block; font-size: 11px; letter-spacing: 5px; margin-top: 3px; padding-left: 3px; }

  .person { position: absolute; left: 45px; top: 114px; color: var(--white); }
  .person__name { font-size: 17px; font-weight: 700; line-height: 1.2; }
  .person__role { font-size: 13px; font-weight: 400; }
  .details { position: absolute; left: 45px; top: 180px; color: var(--white); font-size: 12px; line-height: 16px; }
  .details__company { font-weight: 700; }

  .wordmark { position: absolute; left: 224px; top: 146px; color: var(--white); font-weight: 700; line-height: 1; }
  .wordmark__main { display: block; font-size: 38px; letter-spacing: 0.5px; }
  .wordmark__sub { display: block; font-size: 15px; letter-spacing: 8.6px; margin-top: 6px; padding-left: 5px; font-weight: 600; }
  .website { position: absolute; left: 226px; top: 234px; color: var(--white); font-size: 12px; letter-spacing: 2.2px; }
  .website b { font-weight: 700; }
</style>
</head>
<body>
<main class="canvas">
  <section class="card card--front">
    <div class="band"></div>
    <div class="brand">
      <span class="brand__dot"></span>
      <span class="brand__name"><span class="brand__main">LARCHMERE</span><span class="brand__sub">CONSULTING</span></span>
    </div>
    <div class="person">
      <p class="person__name">Nora Pellin</p>
      <p class="person__role">CEO</p>
    </div>
    <div class="details">
      <p class="details__company">LARCHMERE CONSULTING PTY LIMITED</p>
      <p>ABN 48 312 905 274</p>
      <p>PO Box 418, Hollowbay NSW 2091, Australia</p>
      <p>M +61 412 508 377</p>
      <p>E nora.pellin@larchmereconsulting.com</p>
    </div>
  </section>

  <section class="card card--back">
    <div class="band"></div>
    <p class="wordmark"><span class="wordmark__main">LARCHMERE</span><span class="wordmark__sub">CONSULTING</span></p>
    <p class="website">www.<b>larchmereconsulting</b>.com</p>
  </section>
</main>
</body>
</html>
```